Modern Verdell Tree Care Website

I need a website for a full service Tree Care company. The company provides tree pruning, tree removal, tree preservation, emergency services, stump grinding, and emergency tree services.

Target Market(s)

Customers that need tree services

Industry/Entity Type

Landscaping, Tree Services

Coding

Coded - Design and coding required

Number of Pages Required

5+ page

Font styles to use
Sans Serif

Requirements
Must have
• Good clean design that showcases the services the company provides.
Nice to have
• Services page; contact form, blog, home page, about page

```html
<!DOCTYPE html>
<html lang="en">
<head>
<meta charset="utf-8">
<title>Verdell Tree Care</title>
<link href="https://fonts.googleapis.com/css2?family=Montserrat:wght@300;400;500;600;700;800&display=swap" rel="stylesheet">
<style>
:root{
  --green:#7cb82f;
  --orange:#f9a832;
  --ink:#2b2b2b;
  --muted:#555;
  --cream:#f1f0e7;
  --forest:#3b5a26;
  --white:#fff;
}
*{box-sizing:border-box;margin:0;padding:0}
html,body{width:1200px;height:4367px;overflow:hidden}
body{font-family:'Montserrat',sans-serif;color:var(--ink);background:var(--white);position:relative}
.abs{position:absolute}
.photo{position:absolute}

/* header */
.site-header{position:absolute;left:0;top:0;width:1200px;height:85px;background:var(--white);z-index:5}
.brand{position:absolute;left:90px;top:16px;display:flex;align-items:center;gap:10px}
.brand-mark{width:44px;height:44px;background:var(--orange);border-radius:4px}
.brand-name{font-weight:700;font-size:22px;color:var(--green);line-height:1.1;letter-spacing:.5px}
.main-nav{position:absolute;left:340px;top:34px;display:flex;font-size:13px;font-weight:500;letter-spacing:1.2px}
.main-nav a{color:var(--ink);text-decoration:none;padding:0 30px;border-left:1px solid #ccc;line-height:14px}
.main-nav a:first-child{border-left:none;padding-left:0;color:var(--green);position:relative}
.main-nav a:first-child::after{content:"";position:absolute;left:0;right:30px;bottom:-10px;height:2px;background:var(--green)}
.header-phone{position:absolute;right:0;top:0;width:228px;height:85px;background:var(--green);clip-path:polygon(14% 0,100% 0,100% 100%,0 100%);color:var(--white);font-size:15px;letter-spacing:1.5px;display:flex;align-items:center;padding-left:48px;gap:10px}
.header-phone svg{flex:none}

/* hero */
.hero-photo{left:0;top:85px;width:1200px;height:690px;background:linear-gradient(120deg,#9ccbee 0%,#4d9ae0 45%,#2f6fb9 75%,#3d5a2a 100%);clip-path:polygon(0 0,100% 0,100% 84%,0 98%)}
.hero-wedge{left:0;top:660px;width:1200px;height:120px}
.hero-copy{left:132px;top:228px;color:var(--ink)}
.hero-copy h1{font-weight:300;font-size:50px;line-height:56px;letter-spacing:1px}
.hero-copy h1 b{display:block;font-weight:800}
.hero-copy p{font-size:19px;margin-top:22px;margin-left:4px}
.btn{display:inline-flex;align-items:center;justify-content:center;height:44px;color:var(--white);font-size:12px;font-weight:600;letter-spacing:1px;clip-path:polygon(12% 0,100% 0,88% 100%,0 100%)}
.btn-orange{background:var(--orange)}
.btn-green{background:var(--green)}
.hero-actions{left:124px;top:462px;display:flex;gap:8px}
.hero-actions .btn{width:180px}
.hero-arrow{top:350px;width:24px;height:44px}

/* about */
.about-photo{left:110px;top:770px;width:450px;height:518px;background:linear-gradient(165deg,#c3dba0 0%,#7ea84a 55%,#d98a45 100%)}
.about-copy{left:593px;top:818px;width:520px}
.section-title{font-size:37px;font-weight:800;line-height:40px;letter-spacing:.5px}
.section-title span{font-weight:400;color:var(--green)}
.about-copy .section-title span{display:block}
.about-copy p{font-size:15px;line-height:23px;color:var(--muted);margin-top:30px;padding-left:10px}
.about-copy p + p{margin-top:22px}
.about-copy .btn{width:180px;margin-top:26px;margin-left:4px}

/* services */
.services{left:0;top:1288px;width:1200px;height:709px;background:var(--cream)}
.centered-title{position:absolute;left:0;width:1200px;text-align:center}
.title-rule{position:absolute;width:36px;height:3px;background:var(--green)}
.service-card{position:absolute;width:301px;height:215px;overflow:hidden}
.service-card .photo{inset:0}
.service-card h3{position:absolute;left:0;right:0;bottom:28px;text-align:center;color:var(--white);font-size:17px;font-weight:700;letter-spacing:.3px}
.service-card h3::after{content:"";position:absolute;left:50%;top:30px;width:34px;height:2px;margin-left:-17px;background:var(--white)}
.service-card.is-active{background:rgba(59,90,38,.92);padding:40px 28px;text-align:center;color:var(--white);overflow:visible}
.service-card.is-active h3{position:static;font-size:17px;font-weight:600}
.service-card.is-active h3::after{display:none}
.service-card.is-active p{font-size:10.5px;line-height:16px;margin-top:12px}
.service-card.is-active .btn{width:120px;height:26px;font-size:9px;margin-top:14px}
.active-shadow{position:absolute;left:437px;top:1600px;width:323px;height:73px;background:var(--orange)}

/* why */
.why-tree{left:430px;top:2186px;width:360px;height:306px;background:linear-gradient(180deg,#6aa83e 0%,#3e7422 80%,#5a4a36 100%)}
.feature-icon{position:absolute;width:82px;height:82px;border-radius:50%;display:flex;align-items:center;justify-content:center}
.feature-icon.g{background:var(--green)}
.feature-icon.o{background:var(--orange)}
.feature-label{position:absolute;width:240px;text-align:center;font-size:16px;font-weight:600;line-height:21px;letter-spacing:.3px}

/* blogs */
.blogs{left:0;top:2771px;width:1200px;height:602px;background:var(--cream)}
.blog-card{position:absolute;top:2919px;width:321px;height:387px;background:var(--white);border:1px solid #d9d9d0}
.blog-card .photo{left:0;top:0;width:100%;height:217px}
.blog-date{position:absolute;left:0;top:190px;width:140px;height:27px;background:rgba(249,168,50,.85);color:var(--white);font-size:11px;font-weight:600;letter-spacing:.5px;display:flex;align-items:center;justify-content:center}
.blog-card h3{position:absolute;left:32px;top:245px;width:260px;font-size:16px;font-weight:600;line-height:22px}
.blog-card p{position:absolute;left:32px;top:300px;width:260px;font-size:10.5px;line-height:17px;color:var(--muted)}
.blog-card a{position:absolute;left:32px;top:342px;font-size:13px;font-weight:600;color:var(--green);letter-spacing:.5px;text-decoration:underline}

/* contact */
.contact-bg{left:0;top:3373px;width:1200px;height:676px;background:var(--forest)}
.contact-photo{left:0;top:3373px;width:640px;height:676px;background:linear-gradient(100deg,#c67b3f 0%,#8c6b4a 40%,#556b3c 100%);clip-path:polygon(0 0,100% 0,80% 100%,0 100%)}
.contact-band{left:0;top:3373px;width:1200px;height:110px}
.contact-form{left:646px;top:3524px;width:440px;color:var(--white)}
.contact-form .section-title{color:var(--white)}
.contact-form .section-title span{color:var(--white);font-weight:400}
.field{position:absolute;left:5px;width:432px;height:47px;background:var(--white);color:#666;font-size:12px;padding:17px 25px}
.contact-form .btn{position:absolute;left:10px;top:390px;width:190px;height:44px}

/* footer */
.footer-divider{position:absolute;top:4048px;width:1px;height:319px;background:#e5e5e5}
.footer-head{position:absolute;top:4112px;font-size:16px;font-weight:500;letter-spacing:.5px}
.footer-head::before{content:"";position:absolute;left:-18px;top:-4px;width:8px;height:20px;background:var(--orange);clip-path:polygon(0 0,100% 100%,0 100%)}
.footer-links{position:absolute;left:459px;top:4154px;list-style:none;font-size:12px;line-height:29px}
.footer-links li:first-child{text-decoration:underline}
.contact-line{position:absolute;left:681px;display:flex;gap:14px;font-size:11px;line-height:17px;color:var(--muted)}
.contact-line b{color:var(--ink);font-weight:600}
.socials{position:absolute;left:955px;top:4154px;display:flex;gap:12px}
.socials span{width:26px;height:26px;border-radius:50%;border:2px solid var(--green)}
.copyright{position:absolute;left:122px;top:4222px;font-size:12px;line-height:20px;color:var(--muted)}
</style>
</head>
<body>

<header class="site-header">
  <div class="brand"><span class="brand-mark"></span><span class="brand-name">Verdell<br>Tree Care</span></div>
  <nav class="main-nav">
    <a href="#">HOME</a><a href="#">ABOUT US</a><a href="#">SERVICES</a><a href="#">BLOG</a><a href="#">CONTACT US</a>
  </nav>
  <div class="header-phone">
    <svg width="22" height="22" viewBox="0 0 24 24"><circle cx="12" cy="12" r="12" fill="#fff"/><path d="M8 6l2 0 1 3-1.5 1a8 8 0 0 0 4.5 4.5l1-1.5 3 1v2a2 2 0 0 1-2 2A11 11 0 0 1 6 8a2 2 0 0 1 2-2z" fill="#7cb82f"/></svg>
    (555) 014 2286
  </div>
</header>

<section>
  <div class="photo hero-photo" role="img" aria-label="Arborist in safety gear climbing a tree with a chainsaw against a blue sky"></div>
  <svg class="abs hero-wedge" viewBox="0 0 1200 120" width="1200" height="120"><polygon points="760,60 1200,8 1200,110" fill="#f9a832"/></svg>
  <svg class="abs hero-arrow" style="left:28px" viewBox="0 0 24 44"><polyline points="20,2 3,22 20,42" fill="none" stroke="#7cb82f" stroke-width="3"/></svg>
  <svg class="abs hero-arrow" style="left:1140px" viewBox="0 0 24 44"><polyline points="4,2 21,22 4,42" fill="none" stroke="#fff" stroke-width="3"/></svg>
  <div class="abs hero-copy">
    <h1>VERDELL FOR<b>ALL YOUR TREE</b><b>CARE NEEDS</b></h1>
    <p>Serving Elmsworth and surrounding areas.</p>
  </div>
  <div class="abs hero-actions"><a class="btn btn-orange">CONTACT US</a><a class="btn btn-green">VIEW SERVICES</a></div>
</section>

<section>
  <div class="photo about-photo" role="img" aria-label="Arborists working with ropes among tree branches"></div>
  <div class="abs about-copy">
    <h2 class="section-title">ABOUT VERDELL<span>TREE CARE</span></h2>
    <p>At Verdell Tree Care, we are more than just a tree service company, we are stewards of our beautiful trees. With a passion deeply rooted in arboriculture, we embark on a mission to promote the health, beauty, and safety of your trees and landscapes.</p>
    <p>Whether it's expert tree trimming to enhance aesthetics, meticulous tree removal to mitigate hazards, or comprehensive tree health assessments to ensure safety , we approach each task with unwavering dedication and attention to detail.</p>
    <a class="btn btn-orange">LEARN MORE</a>
  </div>
  <svg class="abs" style="left:870px;top:862px" width="26" height="30" viewBox="0 0 26 30"><polygon points="13,0 26,22 0,22" fill="#7cb82f"/><rect x="11" y="22" width="4" height="8" fill="#7cb82f"/></svg>
</section>

<section>
  <div class="abs services"></div>
  <h2 class="section-title centered-title" style="top:1358px;font-size:34px">SERVICES <span>PROVIDE</span></h2>
  <span class="title-rule" style="left:580px;top:1410px"></span>
  <div class="active-shadow"></div>

  <div class="service-card" style="left:122px;top:1446px"><div class="photo" role="img" aria-label="Pruning shears cutting a branch" style="background:linear-gradient(160deg,#8fae5a,#55733a)"></div><h3>TREE PRUNING</h3></div>
  <div class="service-card is-active" style="left:449px;top:1446px">
    <h3>TREE REMOVAL</h3>
    <p>Lorem ipsum dolor sit amet, consectetur adipiscing elit, sed do eiusmod tempor incididunt ut labore et dolore magna aliqua. Quis ipsum suspendis</p>
    <a class="btn btn-green">LEARN MORE</a>
  </div>
  <div class="service-card" style="left:775px;top:1446px"><div class="photo" role="img" aria-label="Shovel planting a young tree in soil" style="background:linear-gradient(160deg,#9cc26a,#5d4330)"></div><h3>TREE PRESERVATION</h3></div>
  <div class="service-card" style="left:119px;top:1686px"><div class="photo" role="img" aria-label="Stump grinder working on a tree stump" style="background:linear-gradient(160deg,#6f8f4d,#7a5a3a)"></div><h3>STUMP GRINDING</h3></div>
  <div class="service-card" style="left:446px;top:1686px"><div class="photo" role="img" aria-label="Fallen tree after a storm" style="background:linear-gradient(160deg,#a2b98a,#4e6a35)"></div><h3>TREE EMERGENCY SERVICES</h3></div>
  <div class="service-card" style="left:773px;top:1686px"><div class="photo" role="img" aria-label="Arborist installing cabling in a tree canopy" style="background:linear-gradient(160deg,#8fb7d8,#4c6b3a)"></div><h3>CABLING &amp; BRACING</h3></div>
</section>

<section>
  <h2 class="section-title centered-title" style="top:2065px;font-size:34px">WHY CHOOSE <span>VERDELL</span></h2>
  <span class="title-rule" style="left:582px;top:2117px"></span>
  <div class="photo why-tree" role="img" aria-label="Large green leafy tree standing on grass"></div>
  <svg class="abs" style="left:0;top:2150px" width="1200" height="500" viewBox="0 0 1200 500" fill="none" stroke="#7cb82f" stroke-width="1.5">
    <polyline points="355,15 430,15 468,52"/><circle cx="355" cy="15" r="5" fill="#7cb82f"/>
    <polyline points="870,15 790,15 748,58"/><circle cx="870" cy="15" r="5" fill="#7cb82f"/>
    <polyline points="322,162 402,162 430,190"/><circle cx="322" cy="162" r="5" fill="#7cb82f"/>
    <polyline points="892,162 820,162 790,190"/><circle cx="892" cy="162" r="5" fill="#7cb82f"/>
    <polyline points="400,335 440,300 430,300"/><circle cx="400" cy="335" r="5" fill="#7cb82f"/>
    <polyline points="790,300 830,335"/><circle cx="830" cy="335" r="5" fill="#7cb82f"/>
    <polyline points="615,362 615,420"/><circle cx="615" cy="420" r="5" fill="#7cb82f"/>
  </svg>
  <div class="feature-icon g" style="left:256px;top:2124px"><svg width="40" height="40" viewBox="0 0 40 40" fill="none" stroke="#fff" stroke-width="2"><rect x="9" y="6" width="20" height="26" rx="2"/><polyline points="18,25 22,29 30,20"/></svg></div>
  <div class="feature-label" style="left:177px;top:2212px">LICENSED AND INSURED</div>
  <div class="feature-icon g" style="left:874px;top:2132px"><svg width="40" height="40" viewBox="0 0 40 40" fill="none" stroke="#fff" stroke-width="2"><circle cx="20" cy="15" r="9"/><line x1="20" y1="24" x2="20" y2="34"/></svg></div>
  <div class="feature-label" style="left:805px;top:2223px">PROFESSIONAL WORK</div>
  <div class="feature-icon o" style="left:223px;top:2278px"><svg width="40" height="40" viewBox="0 0 40 40" fill="none" stroke="#fff" stroke-width="2"><circle cx="20" cy="20" r="13"/><polyline points="20,12 20,20 26,23"/></svg></div>
  <div class="feature-label" style="left:144px;top:2372px">24 HOUR EMERGENCY<br>SERVICES</div>
  <div class="feature-icon o" style="left:912px;top:2278px"><svg width="40" height="40" viewBox="0 0 40 40" fill="none" stroke="#fff" stroke-width="2"><path d="M10 22a10 10 0 0 1 20 0z"/><rect x="8" y="22" width="24" height="4"/><circle cx="20" cy="31" r="3"/></svg></div>
  <div class="feature-label" style="left:837px;top:2372px">SAFETY IS OUR<br>TOP PRIORITY</div>
  <div class="feature-icon g" style="left:318px;top:2473px"><svg width="40" height="40" viewBox="0 0 40 40" fill="none" stroke="#fff" stroke-width="2"><path d="M20 34s-10-10-10-17a10 10 0 0 1 20 0c0 7-10 17-10 17z"/><circle cx="20" cy="17" r="4"/></svg></div>
  <div class="feature-label" style="left:240px;top:2564px">LOCALLY OWNED<br>&amp; OPERATED</div>
  <div class="feature-icon g" style="left:830px;top:2473px"><svg width="40" height="40" viewBox="0 0 40 40" fill="none" stroke="#fff" stroke-width="2"><rect x="10" y="6" width="20" height="28" rx="2"/><line x1="14" y1="14" x2="26" y2="14"/><line x1="14" y1="20" x2="26" y2="20"/><line x1="14" y1="26" x2="22" y2="26"/></svg></div>
  <div class="feature-label" style="left:751px;top:2564px">FREE ESTIMATE</div>
  <div class="feature-icon o" style="left:578px;top:2583px"><svg width="40" height="40" viewBox="0 0 40 40" fill="none" stroke="#fff" stroke-width="2"><circle cx="20" cy="13" r="5"/><circle cx="11" cy="20" r="4"/><circle cx="29" cy="20" r="4"/><path d="M8 32a12 8 0 0 1 24 0"/></svg></div>
  <div class="feature-label" style="left:500px;top:2677px">LICENSED ARBORIST<br>ON STAFF</div>
</section>

<section>
  <div class="abs blogs"></div>
  <h2 class="section-title abs" style="left:97px;top:2831px;font-size:38px">LATEST <span>BLOGS</span></h2>
  <span class="title-rule" style="left:97px;top:2883px"></span>

  <article class="blog-card" style="left:102px">
    <div class="photo" role="img" aria-label="Chainsaw cutting into a large tree trunk" style="background:linear-gradient(160deg,#bcbab0,#6c5a44)"></div>
    <span class="blog-date">20 MAY 2024</span>
    <h3>Lorem ipsum dolor sit amet consectetur adipiscing</h3>
    <p>Lorem ipsum dolor sit amet, consectetur adipiscing elit, sed do eiusmod tempor incid</p>
    <a>LEARN MORE</a>
  </article>
  <article class="blog-card" style="left:447px">
    <div class="photo" role="img" aria-label="Arborist climbing a tree trunk with harness" style="background:linear-gradient(160deg,#9fbf7a,#4a5e3a)"></div>
    <span class="blog-date">20 MAY 2024</span>
    <h3>Lorem ipsum dolor sit amet consectetur adipiscing</h3>
    <p>Lorem ipsum dolor sit amet, consectetur adipiscing elit, sed do eiusmod tempor incid</p>
    <a>LEARN MORE</a>
  </article>
  <article class="blog-card" style="left:790px">
    <div class="photo" role="img" aria-label="Gardener trimming branches with long loppers" style="background:linear-gradient(160deg,#8cbf58,#3f6b2a)"></div>
    <span class="blog-date">20 MAY 2024</span>
    <h3>Lorem ipsum dolor sit amet consectetur adipiscing</h3>
    <p>Lorem ipsum dolor sit amet, consectetur adipiscing elit, sed do eiusmod tempor incid</p>
    <a>LEARN MORE</a>
  </article>
</section>

<section>
  <div class="abs contact-bg"></div>
  <div class="photo contact-photo" role="img" aria-label="Arborist in helmet and ear protection cutting a trunk with a chainsaw"></div>
  <svg class="abs contact-band" viewBox="0 0 1200 110" width="1200" height="110"><polygon points="0,0 0,110 520,62" fill="#7cb82f"/><polygon points="0,0 1200,0 520,62" fill="#f1f0e7"/></svg>
  <div class="abs contact-form">
    <h2 class="section-title" style="font-size:38px">CONTACT <span>US</span></h2>
    <span class="title-rule" style="left:5px;top:54px"></span>
    <div class="field" style="top:85px">First Name*</div>
    <div class="field" style="top:142px">Email address</div>
    <div class="field" style="top:200px">Phone number</div>
    <div class="field" style="top:257px;height:121px">Leave Message</div>
    <a class="btn btn-orange">SEND MESSAGE</a>
  </div>
</section>

<footer>
  <div class="brand" style="top:4110px;left:120px"><span class="brand-mark" style="width:56px;height:56px"></span><span class="brand-name" style="font-size:28px">Verdell<br>Tree Care</span></div>
  <p class="copyright">Copyright © 2024 Verdell Tree Care<br>All Right Reserved</p>
  <span class="footer-divider" style="left:436px"></span>
  <span class="footer-divider" style="left:658px"></span>
  <span class="footer-divider" style="left:936px"></span>

  <h4 class="footer-head" style="left:459px">NAVIGATION</h4>
  <ul class="footer-links"><li>Home</li><li>About Us</li><li>Services</li><li>Blogs</li><li>Contact</li></ul>

  <h4 class="footer-head" style="left:681px">CONTACT US</h4>
  <div class="contact-line" style="top:4156px">
    <svg width="28" height="28" viewBox="0 0 24 24" fill="none" stroke="#888" stroke-width="1.3"><path d="M6 3l3 0 1.5 4-2 1.5a10 10 0 0 0 7 7l1.5-2 4 1.5v3a2 2 0 0 1-2 2A17 17 0 0 1 4 5a2 2 0 0 1 2-2z"/></svg>
    <div>Phone number<br><b>(555) 014-2286<br>(555) 019-4471</b></div>
  </div>
  <div class="contact-line" style="top:4223px">
    <svg width="28" height="22" viewBox="0 0 28 22" fill="none" stroke="#888" stroke-width="1.3"><rect x="1" y="1" width="26" height="20"/><polyline points="1,1 14,12 27,1"/></svg>
    <div>Email address<br><b>hello@verdelltreecare.com</b></div>
  </div>

  <h4 class="footer-head" style="left:961px">FOLLOW US</h4>
  <div class="socials" aria-label="Social media links"><span></span><span></span><span></span><span></span></div>
</footer>

</body>
</html>
```